Mira Bloom Fitness Coaching Project

I am a personal trainer based in London. My services include one-on-one PT sessions, bootcamps.
I would like the design to be minimalistic. With light colours: white, pink, purple.
I specialise in weight loss, flexibility, mobility.

Tessa Brogan
Personal Trainer
Email: tessa.brogan@quellmail.com
tel: 07700218493
Instagram: Mira Bloom

Target Market(s)

adults, mostly females (age 18-50).

Industry/Entity Type

Fitness

Contact Information for Business Card

Tessa Brogan
Personal Trainer
tel: 07700218493
Instagram: Mira Bloom

Font styles to use
Serif

Colors
eea4c8
fbd4d5
fdf9cf
cfeae6
cee9f5

Requirements
Nice to have
• minimalistic style
• easy to read and remember

```html
<!DOCTYPE html>
<html lang="en">
<head>
<meta charset="utf-8">
<title>Tessa Brogan — Personal Trainer Business Card</title>
<link rel="stylesheet" href="https://fonts.googleapis.com/css2?family=Bodoni+Moda:wght@500&family=Raleway:wght@300&family=EB+Garamond:wght@400;600&display=swap">
<style>
  :root {
    --backdrop: #2a2a2a;
    --front-dark: #0f1510;
    --front-green: #1d2a1b;
    --photo-warm: #8a5a38;
    --photo-light: #e8c9a8;
    --photo-rose: #b8454a;
    --paper: #ffffff;
    --paper-shade: #ececec;
    --ink: #111111;
    --ink-soft: #555555;
    --name-white: #f4f4f4;
  }
  * { box-sizing: border-box; margin: 0; padding: 0; }
  html, body {
    width: 1200px;
    height: 997px;
    overflow: hidden;
  }
  body {
    background: var(--backdrop);
    position: relative;
  }
  .card {
    position: absolute;
    left: 250px;
    width: 700px;
    height: 400px;
    border-radius: 22px;
    overflow: hidden;
  }
  /* Front side */
  .card-front {
    top: 64px;
    background: radial-gradient(ellipse at 25% 70%, var(--front-green), var(--front-dark) 70%);
  }
  .portrait {
    position: absolute;
    top: 0;
    right: 0;
    width: 58%;
    height: 100%;
    background:
      radial-gradient(ellipse at 45% 40%, var(--photo-light) 0%, var(--photo-warm) 38%, transparent 68%),
      radial-gradient(ellipse at 85% 85%, var(--photo-rose) 0%, transparent 40%),
      linear-gradient(90deg, var(--front-dark) 0%, #3b2a1c 30%, #5a3b26 60%, #6b4a33 100%);
  }
  .identity {
    position: absolute;
    left: 62px;
    bottom: 92px;
    color: var(--name-white);
  }
  .identity-name {
    font-family: "Bodoni Moda", serif;
    font-weight: 500;
    font-size: 40px;
    letter-spacing: 1px;
    text-transform: uppercase;
    line-height: 1;
  }
  .identity-role {
    font-family: "Raleway", sans-serif;
    font-weight: 300;
    font-size: 17px;
    letter-spacing: 5px;
    margin-top: 8px;
    padding-left: 40px;
  }
  /* Back side */
  .card-back {
    top: 524px;
    background: linear-gradient(160deg, var(--paper) 0%, var(--paper) 55%, var(--paper-shade) 100%);
  }
  .back-rule {
    position: absolute;
    left: 62px;
    top: 0;
    width: 2px;
    height: 100%;
    background: var(--ink);
  }
  .contact {
    position: absolute;
    left: 78px;
    bottom: 72px;
    font-family: "EB Garamond", serif;
  }
  .contact-list {
    list-style: none;
    color: var(--ink-soft);
    font-size: 17px;
    line-height: 1.45;
  }
  .services {
    margin-top: 16px;
    font-weight: 600;
    font-size: 18px;
    color: var(--ink);
  }
</style>
</head>
<body>
  <section class="card card-front" aria-label="Card front">
    <div class="portrait" role="img" aria-label="Portrait photograph of the trainer, backlit in warm sunlight"></div>
    <div class="identity">
      <h1 class="identity-name">Tessa Brogan</h1>
      <p class="identity-role">Personal trainer</p>
    </div>
  </section>

  <section class="card card-back" aria-label="Card back">
    <div class="back-rule"></div>
    <div class="contact">
      <ul class="contact-list">
        <li>Tel: 07700218493</li>
        <li>tessa.brogan@quellmail.com</li>
        <li>www.snapfolio.com/Mira_Bloom</li>
      </ul>
      <p class="services">Weight Loss &nbsp;•&nbsp; Flexibility &nbsp;•&nbsp; Mobility</p>
    </div>
  </section>
</body>
</html>
```